Business card design Needed for new logo / Construction business, home extensions and new builds

We need a business card design using our new logo files which i will attach to this project :)

We are a small construction business specialising in home extensions, new builds and property development. We are very ambitious and would appreciate professional and elegant designs for our new business card.

Very serious about using the services on MakerQuarry and recently acquired our new logo from here :)

Please get involved, i will feedback when i can as i am very busy but can respond daily, thanks

Target Market(s)

People that want to build onto their houses, new building developments or adding too their existing property

Industry/Entity Type

Construction

Contact Information for Business Card

Renwick Tolliver Construction, Lionel Ashby (Managing Director), Tel 07822254961, email - info@renwick-tolliver, www.renwick-tolliver.co.uk

Colors

Designer to choose colors to be used in the design.

Requirements
Must have
• I like a deep grey on the back please. A lot of you have provided black from and back, try mixing things up a little. The black looks cool 😎 Thanks

```html
<!DOCTYPE html>
<html lang="en">
<head>
<meta charset="utf-8">
<title>Renwick Tolliver Construction – Business Card</title>
<link rel="stylesheet" href="https://fonts.googleapis.com/css2?family=Cinzel:wght@500&family=Montserrat:wght@400;700&display=swap">
<style>
  :root {
    --stage: #5a5b5e;
    --card-black: #141414;
    --card-deep-grey: #2f3033;
    --pattern-light: #38393c;
    --pattern-dark: #28292b;
    --gold: #e0a82e;
    --gold-light: #f5cf6a;
    --silver: #c9cacc;
    --silver-light: #eeeeef;
    --white: #f2f2f2;
  }
  * { margin: 0; padding: 0; box-sizing: border-box; }
  html, body { width: 1200px; height: 689px; overflow: hidden; }
  body {
    background: var(--stage);
    position: relative;
    font-family: "Montserrat", sans-serif;
  }
  .card {
    position: absolute;
    top: 190px;
    width: 540px;
    height: 309px;
    border-radius: 16px;
    overflow: hidden;
  }
  .card-back { left: 40px; background: var(--card-deep-grey); }
  .card-front { left: 620px; background: var(--card-black); }

  .back-pattern {
    position: absolute; inset: 0;
    background: radial-gradient(ellipse at 50% 45%, var(--pattern-light), var(--pattern-dark));
  }
  .wordmark {
    position: absolute;
    display: flex;
    flex-direction: column;
    align-items: center;
    font-family: "Cinzel", serif;
    font-weight: 500;
    color: var(--gold);
    text-align: center;
    line-height: 1.15;
    white-space: nowrap;
  }
  .wordmark .mark-square {
    width: 14px; height: 14px;
    background: var(--gold);
    margin-bottom: 14px;
  }
  .card-back .wordmark {
    left: 0; right: 0; top: 92px;
    font-size: 34px;
    letter-spacing: 1px;
  }
  .card-back .wordmark .tagline { font-size: 22px; letter-spacing: 4px; }

  .card-front .wordmark {
    left: 20px; width: 300px; top: 92px;
    font-size: 24px;
  }
  .card-front .wordmark .tagline { font-size: 16px; letter-spacing: 3px; }

  .divider {
    position: absolute;
    left: 330px; top: 40px;
    width: 1.5px; height: 150px;
    background: var(--gold);
  }
  .person { position: absolute; left: 350px; top: 48px; }
  .person-name { font-weight: 700; font-size: 19px; color: var(--gold); }
  .person-role { font-size: 12px; color: var(--white); margin-top: 3px; }

  .contact-list {
    position: absolute; left: 350px; top: 128px;
    list-style: none;
    font-size: 11.5px; color: var(--white);
  }
  .contact-list li {
    display: flex; align-items: center; gap: 7px;
    margin-bottom: 6px;
  }
  .contact-list svg { width: 11px; height: 11px; flex: none; }

  .base-bands { position: absolute; left: 0; bottom: 0; width: 540px; height: 80px; }
</style>
</head>
<body>

<section class="card card-back" aria-label="Card back">
  <div class="back-pattern" role="img" aria-label="Tonal repeating monogram pattern in deep grey"></div>
  <div class="wordmark">
    <span class="mark-square"></span>
    <span>Renwick Tolliver</span>
    <span class="tagline">Construction</span>
  </div>
</section>

<section class="card card-front" aria-label="Card front">
  <div class="wordmark">
    <span class="mark-square"></span>
    <span>Renwick Tolliver</span>
    <span class="tagline">Construction</span>
  </div>

  <div class="divider"></div>

  <div class="person">
    <p class="person-name">Lionel Ashby</p>
    <p class="person-role">Managing Director</p>
  </div>

  <ul class="contact-list">
    <li>
      <svg viewBox="0 0 12 12" aria-hidden="true"><path fill="var(--gold)" d="M2.5 1h2l1 3-1.4 1a6 6 0 0 0 2.9 2.9l1-1.4 3 1v2a1.5 1.5 0 0 1-1.5 1.5A9.5 9.5 0 0 1 1 2.5 1.5 1.5 0 0 1 2.5 1z"/></svg>
      <span>07822254961</span>
    </li>
    <li>
      <svg viewBox="0 0 12 12" aria-hidden="true"><rect x="0.5" y="2.5" width="11" height="7.5" rx="1" fill="var(--gold)"/><path d="M1 3l5 4 5-4" fill="none" stroke="var(--card-black)" stroke-width="1"/></svg>
      <span>info@renwick-tolliver</span>
    </li>
    <li>
      <svg viewBox="0 0 12 12" aria-hidden="true"><circle cx="6" cy="6" r="5.2" fill="none" stroke="var(--gold)" stroke-width="1.2"/><ellipse cx="6" cy="6" rx="2.2" ry="5.2" fill="none" stroke="var(--gold)" stroke-width="1"/><path d="M1 6h10" stroke="var(--gold)" stroke-width="1"/></svg>
      <span>www.renwick-tolliver.co.uk</span>
    </li>
  </ul>

  <svg class="base-bands" viewBox="0 0 540 80" aria-hidden="true">
    <defs>
      <linearGradient id="silverBand" x1="0" x2="1" y1="0" y2="0">
        <stop offset="0" stop-color="var(--silver)"/>
        <stop offset="0.5" stop-color="var(--silver-light)"/>
        <stop offset="1" stop-color="var(--silver)"/>
      </linearGradient>
      <linearGradient id="goldBand" x1="0" x2="1" y1="0" y2="0">
        <stop offset="0" stop-color="var(--gold)"/>
        <stop offset="0.5" stop-color="var(--gold-light)"/>
        <stop offset="1" stop-color="var(--gold)"/>
      </linearGradient>
    </defs>
    <path d="M0 70 H345 L365 50 H372 L345 80 H0 Z" fill="url(#silverBand)"/>
    <path d="M380 50 H540 V80 H352 Z" fill="url(#goldBand)"/>
  </svg>
</section>

</body>
</html>
```